Bureau for Innovation and Outreach Needs a Graphically Designed Powerpoint Template

We are from Bureau for Innovation and Outreach (BIO), part of a medical school. BIO contributes to the medical school by overseeing and managing intellectual property generated by researchers at the medical school, and also works to ensure optimal commercial outcomes for all inventions arising from the medical school. We want a graphically designed powerpoint presentation template to describe how BIO is involved in a researcher’s journey to major scientific contributions. The journey should be represented in the form of a main road (or pathway). Along the main road, there will be smaller roads branching out, each representing one of the researcher’s major scientific contributions. We will be inputting text details of each major scientific contribution near each of the small road branches. The smaller road branches will also need to be removable / editable. This is because we might need to send the template to different researchers to input details of their major scientific contributions, and each researcher will have a different number of them. Hence, you can possibly place around 6 branches along the main road, but we want to be able to remove the branches should we need to. Removal of the branches (design elements) should still result in a seamless image in powerpoint. We also want to be able to add and edit text in the design template. The start of the main road should contain a placeholder for us to place the researcher’s photo. The end of the road will lead to one of the major scientific contributions. Please see the uploaded sketch to have an idea of what we are looking to get. We welcome deviations and changes to the design as shown from the sketch, as long as the design is able to convey what we have described above. As this powerpoint template will be used for presentation to the senior management, we need it to look beautiful yet professional.

Target Market(s)

Researcher, Scientist

Industry/Entity Type

School

Font styles to use
Serif
Sans Serif

Requirements
Must have
• A main road or pathway as mentioned in the project description.
Nice to have
• We will leave the "nice to haves" to be decided by the designer.
Should not have
• Trees

```html
<!DOCTYPE html>
<html lang="en">
<head>
<meta charset="utf-8">
<title>BIO services – a researcher's journey</title>
<link rel="stylesheet" href="https://fonts.googleapis.com/css2?family=Playfair+Display:wght@400;700;900&family=Roboto:wght@300;400;500&display=swap">
<style>
:root{
  --teal:#0aa58f;
  --teal-soft:#1fb5a0;
  --blue:#1f6fb5;
  --blue-deep:#1a5fa6;
  --ink:#1d1d1f;
  --grey:#5f5f64;
  --grey-light:#a2a2a7;
  --paper:#ffffff;
  --stage:#f3f3f4;
  --label-blue:#3aa0d8;
}
*{box-sizing:border-box;margin:0;padding:0}
html,body{width:1200px;height:1200px;overflow:hidden}
body{position:relative;background:var(--stage);font-family:"Roboto",Arial,sans-serif;color:var(--ink)}
.backdrop{position:absolute;inset:0}
.slide{position:absolute;background:var(--paper);box-shadow:0 6px 14px rgba(0,0,0,.22)}
.slide--main{left:80px;top:80px;width:1040px;height:585px;
  background:linear-gradient(135deg,#fafafa 0%,#ffffff 45%,#f0f0f0 100%)}
.title{position:absolute;left:48px;top:44px;font-family:"Playfair Display",Georgia,serif;line-height:1}
.title__main{display:block;font-size:48px;font-weight:400;color:var(--ink)}
.title__sub{display:block;margin-top:0;padding-bottom:10px;font-size:45px;line-height:1.05;font-weight:900;letter-spacing:-.5px;
  background:linear-gradient(90deg,var(--blue) 0%,var(--teal) 100%);-webkit-background-clip:text;background-clip:text;color:transparent}
.profile{position:absolute;left:47px;top:158px;width:139px;height:367px;border-radius:0 0 10px 0;
  background:linear-gradient(170deg,var(--blue-deep) 0%,#2a86b3 60%,#2aa1a0 100%);color:#fff;padding:15px 15px 0 15px}
.profile__photo{width:110px;height:109px;background:linear-gradient(160deg,#c9d6dc,#b9786a 55%,#e9e3df)}
.profile__name{margin-top:13px;font-family:"Playfair Display",Georgia,serif;font-weight:700;font-size:14.5px;line-height:1.3}
.profile__rule{width:28px;height:2px;background:#fff;margin-top:21px}
.profile__label{margin-top:5px;font-size:10px;font-weight:500}
.profile__value{font-size:10px;font-weight:300}
.profile__list{list-style:none;font-size:10px;font-weight:300}
.profile__list li{padding-left:24px;position:relative;line-height:13px}
.profile__list li::before{content:"•";position:absolute;left:2px}
.phase{position:absolute;font-family:"Playfair Display",Georgia,serif;color:var(--grey-light);line-height:1.2}
.phase__num{font-size:14px}
.phase__name{font-size:16px;font-weight:700}
.timeline{position:absolute;left:0;top:0;width:1040px;height:585px}
.card{position:absolute;width:153px;height:148px;background:var(--paper);padding:10px 10px;
  box-shadow:2px 3px 6px rgba(0,0,0,.22)}
.card__title{font-family:"Playfair Display",Georgia,serif;font-weight:700;font-size:11px;line-height:1.2;color:var(--ink)}
.card__body{margin-top:13px;font-size:10.3px;font-weight:300;line-height:13px;color:var(--grey);white-space:nowrap}
.card__icon{position:absolute;right:10px;bottom:10px;width:22px;height:22px}
.caption{position:absolute;left:80px;top:748px;font-size:20px;font-weight:300;line-height:24.5px;color:var(--ink)}
.slide--icons{top:838px;width:502px;height:282px;background:linear-gradient(135deg,#f7f7f7,#fff 50%,#efefef)}
.slide--icons-a{left:80px}
.slide--icons-b{left:618px}
.icons__title{position:absolute;left:11px;top:12px;font-family:"Playfair Display",Georgia,serif;font-weight:700;font-size:10px;color:var(--blue)}
.icons__group{position:absolute;font-size:9px;color:var(--label-blue)}
.icons__grid{position:absolute}
.icons__footer{position:absolute;left:23px;bottom:17px;font-size:6px;color:var(--grey-light)}
.icons__page{position:absolute;right:23px;bottom:17px;font-size:6px;color:var(--grey-light)}
.magnifier{position:absolute;left:0;top:0;width:1200px;height:1200px;pointer-events:none}
</style>
</head>
<body>

<svg class="backdrop" width="1200" height="1200" viewBox="0 0 1200 1200" aria-hidden="true">
  <polygon points="1200,0 1200,1200 0,1200" fill="#0aa58f"/>
</svg>

<section class="slide slide--main">
  <h1 class="title">
    <span class="title__main">BIO services</span>
    <span class="title__sub">/ a researcher’s journey</span>
  </h1>

  <aside class="profile">
    <div class="profile__photo" role="img" aria-label="Portrait photo of the researcher"></div>
    <p class="profile__name">Researcher’s name PhD.</p>
    <div class="profile__rule"></div>
    <p class="profile__label">Institution</p>
    <p class="profile__value">Lorem ipsum</p>
    <div class="profile__rule" style="margin-top:20px"></div>
    <p class="profile__label">Research subjects</p>
    <ul class="profile__list"><li>Lorem ipsum</li><li>Lorem ipsum</li><li>Lorem ipsum</li></ul>
  </aside>

  <svg class="timeline" viewBox="0 0 1040 585" aria-hidden="true">
    <defs>
      <linearGradient id="road" gradientUnits="userSpaceOnUse" x1="200" y1="0" x2="994" y2="0">
        <stop offset="0" stop-color="#1f6fb5"/><stop offset="1" stop-color="#1fb5a0"/>
      </linearGradient>
      <g id="node">
        <circle r="10" fill="#fff" stroke="#444" stroke-width="1"/>
        <circle r="6.5" fill="none" stroke="#444" stroke-width="1"/>
        <circle r="3.5" fill="#333"/>
      </g>
    </defs>
    <rect class="road" x="200" y="339" width="794" height="4" fill="url(#road)"/>
    <line x1="230" y1="341" x2="230" y2="393" stroke="#444" stroke-width="1"/>
    <line x1="427" y1="308" x2="427" y2="341" stroke="#444" stroke-width="1"/>
    <line x1="625" y1="341" x2="625" y2="393" stroke="#444" stroke-width="1"/>
    <line x1="823" y1="308" x2="823" y2="341" stroke="#444" stroke-width="1"/>
    <use href="#node" x="230" y="341"/>
    <use href="#node" x="427" y="341"/>
    <use href="#node" x="625" y="341"/>
    <use href="#node" x="823" y="341"/>
  </svg>

  <div class="phase" style="left:199px;top:284px"><div class="phase__num">Phase 1</div><div class="phase__name">/Lorem ipsum</div></div>
  <div class="phase" style="left:596px;top:284px"><div class="phase__num">Phase 2</div><div class="phase__name">/Lorem ipsum</div></div>

  <article class="card" style="left:418px;top:160px">
    <h2 class="card__title">Major scientific<br>constribution</h2>
    <p class="card__body">Lorem ipsum dolor sit amet,<br>consectetur adipiscing elit.<br>Ut ornare nunc nec lectus<br>aliquam, eget accumsan<br>felis fermentum.</p>
    <svg class="card__icon" viewBox="0 0 22 22"><path d="M3 21V3h16l-4 5 4 5H3" fill="none" stroke="#0aa58f" stroke-width="1.2"/></svg>
  </article>
  <article class="card" style="left:812px;top:160px">
    <h2 class="card__title">Major scientific<br>constribution</h2>
    <p class="card__body">Lorem ipsum dolor sit amet,<br>consectetur adipiscing elit.<br>Ut ornare nunc nec lectus<br>aliquam, eget accumsan<br>felis fermentum.</p>
    <svg class="card__icon" viewBox="0 0 22 22"><path d="M3 21V3h16l-4 5 4 5H3" fill="none" stroke="#0aa58f" stroke-width="1.2"/></svg>
  </article>
  <article class="card" style="left:221px;top:378px">
    <h2 class="card__title">BIO xyz<br>Project</h2>
    <p class="card__body">Lorem ipsum dolor sit amet,<br>consectetur adipiscing elit.<br>Ut ornare nunc nec lectus<br>aliquam, eget accumsan<br>felis fermentum.</p>
    <svg class="card__icon" viewBox="0 0 22 22"><path d="M21 2L1 10l8 3 3 8zM21 2L9 13" fill="none" stroke="#1f6fb5" stroke-width="1.2" stroke-linejoin="round"/></svg>
  </article>
  <article class="card" style="left:616px;top:378px">
    <h2 class="card__title">Major scientific<br>constribution</h2>
    <p class="card__body">Lorem ipsum dolor sit amet,<br>consectetur adipiscing elit.<br>Ut ornare nunc nec lectus<br>aliquam, eget accumsan<br>felis fermentum.</p>
    <svg class="card__icon" viewBox="0 0 22 22"><path d="M3 21V3h16l-4 5 4 5H3" fill="none" stroke="#0aa58f" stroke-width="1.2"/></svg>
  </article>
</section>

<p class="caption">Additional slides with changeable<br>[size AND color] icons to keep a<br>coherent design</p>

<svg width="0" height="0" style="position:absolute" aria-hidden="true">
  <defs>
    <pattern id="icons-a" width="13" height="14.5" patternUnits="userSpaceOnUse">
      <circle cx="5" cy="5" r="3.8" fill="none" stroke="#666" stroke-width=".8"/>
      <path d="M3.3 5h3.4" stroke="#666" stroke-width=".8"/>
    </pattern>
    <pattern id="icons-b" width="13" height="14.5" patternUnits="userSpaceOnUse">
      <rect x="1.5" y="1.5" width="7.5" height="7" fill="none" stroke="#666" stroke-width=".8"/>
      <path d="M3 4h4.5M3 6h3" stroke="#666" stroke-width=".7"/>
    </pattern>
    <pattern id="icons-c" width="13" height="14.5" patternUnits="userSpaceOnUse">
      <path d="M1.5 8.5h8l-1-5h-6z M3.5 3.5a2 2 0 0 1 4 0" fill="none" stroke="#666" stroke-width=".8"/>
    </pattern>
    <pattern id="icons-d" width="13" height="14.5" patternUnits="userSpaceOnUse">
      <path d="M2.5 8a2.2 2.2 0 0 1 .5-4.3 3 3 0 0 1 5.5 1A1.8 1.8 0 0 1 8.5 8z" fill="none" stroke="#666" stroke-width=".8"/>
    </pattern>
  </defs>
</svg>

<section class="slide slide--icons slide--icons-a">
  <p class="icons__title">Icons</p>
  <p class="icons__group" style="left:11px;top:44px">Arrows</p>
  <p class="icons__group" style="left:171px;top:44px">Basic</p>
  <svg class="icons__grid" style="left:11px;top:58px" width="160" height="174" aria-hidden="true"><rect width="160" height="174" fill="url(#icons-a)"/></svg>
  <svg class="icons__grid" style="left:171px;top:58px" width="320" height="188" aria-hidden="true"><rect width="320" height="188" fill="url(#icons-b)"/></svg>
  <p class="icons__footer">The quick, brown fox jumps over a lazy dog.</p>
  <p class="icons__page">3</p>
</section>

<section class="slide slide--icons slide--icons-b">
  <p class="icons__title">Icons</p>
  <p class="icons__group" style="left:11px;top:44px">Ecommerce</p>
  <p class="icons__group" style="left:170px;top:44px">Music</p>
  <p class="icons__group" style="left:331px;top:44px">Software</p>
  <p class="icons__group" style="left:170px;top:122px">Weather</p>
  <svg class="icons__grid" style="left:11px;top:58px" width="156" height="116" aria-hidden="true"><rect width="156" height="116" fill="url(#icons-c)"/></svg>
  <svg class="icons__grid" style="left:170px;top:58px" width="156" height="44" aria-hidden="true"><rect width="156" height="44" fill="url(#icons-a)"/></svg>
  <svg class="icons__grid" style="left:170px;top:136px" width="156" height="102" aria-hidden="true"><rect width="156" height="102" fill="url(#icons-d)"/></svg>
  <svg class="icons__grid" style="left:331px;top:58px" width="156" height="130" aria-hidden="true"><rect width="156" height="130" fill="url(#icons-b)"/></svg>
  <p class="icons__footer">The quick, brown fox jumps over a lazy dog.</p>
  <p class="icons__page">4</p>
</section>

<svg class="magnifier" viewBox="0 0 1200 1200" aria-hidden="true">
  <defs>
    <linearGradient id="cone" x1="1" y1="0" x2="0" y2="1">
      <stop offset="0" stop-color="#777" stop-opacity=".85"/><stop offset="1" stop-color="#999" stop-opacity=".35"/>
    </linearGradient>
    <clipPath id="lens"><circle cx="466" cy="816" r="79"/></clipPath>
  </defs>
  <polygon points="395,780 335,985 345,995 520,880" fill="url(#cone)"/>
  <circle cx="466" cy="816" r="79" fill="#fff"/>
  <g clip-path="url(#lens)" fill="none" stroke="#333" stroke-width="1.6">
    <circle cx="413" cy="770" r="6"/><path d="M403 770h4M413 767v6M410 770h6"/>
    <circle cx="470" cy="765" r="6"/><path d="M441 765h23M448 765v5M455 765v4"/>
    <rect x="498" y="757" width="34" height="17"/><path d="M501 762h28M501 766h28M501 770h28"/>
    <circle cx="402" cy="819" r="9"/><path d="M402 814v10M397 819h10M409 826l11 12"/>
    <rect x="441" y="812" width="36" height="24"/><path d="M441 812l18 13 18-13"/>
    <rect x="503" y="814" width="31" height="20"/><path d="M497 808h31v20M503 814l15 10 16-10"/>
    <rect x="406" y="870" width="17" height="30"/><rect x="443" y="872" width="34" height="30"/><path d="M448 872v30M470 872v30"/>
    <rect x="503" y="872" width="26" height="30"/>
  </g>
</svg>

</body>
</html>
```